Postcard design to acquire new clients for my Property Management Company

I'm looking for a postcard design that I can send to prospective clients detailing information about my company and services.
Postcard should be eye catching and contain information from www.bramblecrestpm.com. I've provided a few screen shots for the most important information and my logo.
Target Market(s)
Real Estate
Industry/Entity Type
Real Estate
Font styles to use
Sans Serif
Requirements
Must have
- Must be eye catching!! this will be a direct mail piece - I'd like for the card to be read and not tossed in the trash immediately.
Design que from the logo.
A place to write / print the receipts name and address.
our physical address - 2387 Hollow Pine Road, Lubbock, TX 79852.
Should not have
- the contact information on the business card is not accurate - please use info from website.

```html
<!DOCTYPE html>
<html lang="en">
<head>
<meta charset="utf-8">
<title>Bramblecrest Property Management – Postcard</title>
<link href="https://fonts.googleapis.com/css2?family=Mulish:wght@400;600;700;800&family=Roboto+Condensed:wght@400;700&family=Great+Vibes&display=swap" rel="stylesheet">
<style>
  :root{
    --brand-blue:#0f4c8a;
    --brand-blue-dark:#0b3d72;
    --ink-gray:#555a60;
    --band-gray:#d9d9da;
    --page-bg:#eeeeee;
    --card-white:#ffffff;
    --soft-gray:#f1f1f2;
    --line-gray:#8c8c8c;
  }
  *{box-sizing:border-box;margin:0;padding:0}
  html,body{width:1200px;height:660px;overflow:hidden}
  body{background:var(--page-bg);font-family:"Mulish",sans-serif;position:relative}

  .postcard{position:absolute;top:140px;width:570px;height:380px;background:var(--card-white);overflow:hidden}
  .postcard--front{left:20px}
  .postcard--back{left:610px}
  .shape-layer{position:absolute;inset:0;width:100%;height:100%}

  /* FRONT */
  .front-bg{position:absolute;inset:0;background:linear-gradient(120deg,#fafafa 0%,var(--soft-gray) 100%)}
  .brand{position:absolute;left:26px;top:26px;color:var(--brand-blue);font-weight:700;line-height:1}
  .brand__name{display:block;font-size:19px;letter-spacing:2.6px}
  .brand__tag{display:block;font-size:8.3px;letter-spacing:2.2px;margin-top:3px}
  .headline{position:absolute;left:26px;top:70px;color:var(--brand-blue);font-weight:400;font-size:20px;line-height:19px;text-transform:uppercase}
  .headline__script{display:block;font-family:"Great Vibes",cursive;text-transform:none;color:#9a9ea3;font-size:22px;line-height:14px;margin-left:-4px;margin-top:1px}
  .headline__city{display:block;margin-top:-2px}
  .intro{position:absolute;left:26px;top:155px;width:200px;font-size:9.4px;line-height:11px;color:var(--brand-blue)}

  .plans{position:absolute;left:22px;top:190px;display:flex;gap:7px}
  .plan{position:relative;width:89px;height:172px;border-radius:5px;background:linear-gradient(180deg,#e2e2e3 0%,#f5f5f5 45%,#c9c9cb 100%);box-shadow:0 4px 4px -2px rgba(0,0,0,.35);text-align:center;padding-top:8px}
  .plan__title{color:var(--brand-blue);font-weight:800;font-size:11.5px;line-height:10.5px;text-transform:uppercase}
  .plan__note{font-size:5.6px;font-weight:700;color:var(--ink-gray);margin-top:4px}
  .plan__rule{width:32px;height:1px;background:var(--brand-blue);margin:6px auto 5px}
  .plan__rate{color:var(--brand-blue);font-weight:800;font-size:23px;line-height:22px}
  .plan__basis{font-size:5.6px;font-weight:700;color:var(--ink-gray)}
  .plan__list{list-style:none;font-family:"Roboto Condensed",sans-serif;font-size:5.6px;line-height:8.8px;color:var(--ink-gray);margin-top:9px}

  .photo{position:absolute;inset:0}
  .contact{position:absolute;left:345px;top:277px;color:#fff}
  .contact__label{font-weight:400;font-size:13px;line-height:14px}
  .contact__value{font-weight:700;font-size:18.5px;line-height:20px;margin-bottom:4px}
  .contact__value--email{font-size:17px}

  /* BACK */
  .services-head{position:absolute;left:28px;top:15px;color:var(--brand-blue)}
  .services-head__title{font-weight:800;font-size:19px;line-height:20px;letter-spacing:.2px}
  .services-head__sub{font-style:italic;font-size:9.5px;color:var(--ink-gray);margin-top:1px}
  .services{position:absolute;left:26px;top:62px;width:240px;display:grid;grid-template-columns:112px 112px;column-gap:10px;row-gap:7px;color:#fff}
  .service__name{display:flex;align-items:center;gap:4px;font-weight:700;font-size:8.6px;line-height:10px;margin-bottom:3px;white-space:nowrap}
  .service__name svg{width:9px;height:9px;flex:none}
  .service__text{font-family:"Roboto Condensed",sans-serif;font-size:6.4px;line-height:7.8px;text-align:justify;min-height:47px}
  .back-brand{position:absolute;left:30px;top:326px;color:var(--brand-blue);font-weight:700;line-height:1}
  .back-brand .brand__name{font-size:19px;letter-spacing:2.4px}
  .back-brand .brand__tag{font-size:8.2px;letter-spacing:2.3px}

  .stamp-box{position:absolute;left:466px;top:32px;width:68px;height:67px;border:1px solid #777}
  .address-block{position:absolute;left:324px;top:138px;width:210px}
  .address-block__to{font-weight:800;font-size:10px;color:#111}
  .address-line{height:1px;background:var(--line-gray);margin-top:26px}
  .address-line:first-of-type{margin-top:24px}
  .back-contact{position:absolute;left:324px;top:318px;color:var(--brand-blue-dark);font-weight:800}
  .back-contact__phone{font-size:23px;line-height:24px}
  .back-contact__web{font-size:11.2px;line-height:13px;text-transform:uppercase}
  .back-contact__address{font-size:8.6px;line-height:11px;font-weight:700;color:var(--ink-gray);margin-top:3px}
</style>
</head>
<body>

<section class="postcard postcard--front">
  <div class="front-bg"></div>

  <svg class="shape-layer photo" viewBox="0 0 570 380" preserveAspectRatio="none">
    <defs>
      <linearGradient id="photoTone" x1="0" y1="0" x2="1" y2="1">
        <stop offset="0" stop-color="#e6e1d8"/>
        <stop offset=".45" stop-color="#c9b8a4"/>
        <stop offset="1" stop-color="#8f6e58"/>
      </linearGradient>
    </defs>
    <polygon role="img" aria-label="Photo of a smiling property manager handing house keys to a new tenant in a bright home" points="226,0 570,0 570,265 307,265" fill="url(#photoTone)"/>
    <polygon points="307,265 570,265 570,380 342,380" fill="var(--brand-blue)"/>
  </svg>

  <div class="brand">
    <span class="brand__name">BRAMBLECREST</span>
    <span class="brand__tag">PROPERTY MANAGEMENT</span>
  </div>

  <h1 class="headline">Property<br>Management
    <span class="headline__script">Across</span>
    <span class="headline__city">Lubbock, TX</span>
  </h1>
  <p class="intro">Maximize your financial returns with support from our rental specialists</p>

  <div class="plans">
    <article class="plan">
      <h2 class="plan__title">Lease<br>Only</h2>
      <p class="plan__note">You Just need Tenants</p>
      <div class="plan__rule"></div>
      <p class="plan__rate">9%</p>
      <p class="plan__basis">of annual lease</p>
      <ul class="plan__list">
        <li>Professional Photography</li>
        <li>Marketing&amp;Advertising</li>
        <li>Property Showings</li>
        <li>Tenant Screening &amp; Qualifications</li>
        <li>Lease Execution</li>
        <li>move in coordination</li>
      </ul>
    </article>
    <article class="plan">
      <h2 class="plan__title">Full<br>Service</h2>
      <p class="plan__note">Our Most Popular</p>
      <div class="plan__rule"></div>
      <p class="plan__rate">10%</p>
      <p class="plan__basis">of monthly rent</p>
      <ul class="plan__list">
        <li>Includes Leasing Service</li>
        <li>24/7 Emergency Response</li>
        <li>Move In &amp; Out Inspections</li>
        <li>Professional Lease Enforcement</li>
        <li>Schedule &amp; Oversee all Repairs</li>
        <li>Pay all Invoices</li>
        <li>Monthly &amp; Year End Statements</li>
        <li>Annual Market Rent Analysis</li>
      </ul>
    </article>
    <article class="plan">
      <h2 class="plan__title">Premium<br>Service</h2>
      <p class="plan__note">Our Premier Service</p>
      <div class="plan__rule"></div>
      <p class="plan__rate">12%</p>
      <p class="plan__basis">of monthly rent</p>
      <ul class="plan__list">
        <li>Includes Full Service Features</li>
        <li>Professional Video Marketing</li>
        <li>Home Warranty Coordination</li>
        <li>Tenant Retention Program</li>
      </ul>
    </article>
  </div>

  <div class="contact">
    <p class="contact__label">Give us a call now</p>
    <p class="contact__value">(806) 555-0147</p>
    <p class="contact__label">Email us</p>
    <p class="contact__value contact__value--email">info@bramblecrestpm.com</p>
  </div>
</section>

<section class="postcard postcard--back">
  <svg class="shape-layer" viewBox="0 0 570 380" preserveAspectRatio="none">
    <polygon points="0,0 285,0 285,5 0,5" fill="var(--brand-blue)"/>
    <polygon points="0,5 291,5 288,54 0,54" fill="var(--band-gray)"/>
    <polygon points="0,54 282,54 269,317 0,317" fill="var(--brand-blue)"/>
    <polygon points="0,317 276,317 273,373 0,373" fill="var(--band-gray)"/>
    <polygon points="0,373 266,373 265,380 0,380" fill="var(--brand-blue)"/>
  </svg>

  <header class="services-head">
    <h2 class="services-head__title">DISCOVER OUR SERVICES</h2>
    <p class="services-head__sub">We offer full-service property management solutions</p>
  </header>

  <div class="services">
    <div class="service">
      <h3 class="service__name"><svg viewBox="0 0 10 10"><path d="M5 1 1 5h1.3v4h2.2V6.5h1V9h2.2V5H9z" fill="#fff"/></svg>Property Marketing</h3>
      <p class="service__text">Tired of waiting for weeks on end, hoping to find a new tenant? Let us take over your marketing for you and we'll find a qualified renter quickly.</p>
    </div>
    <div class="service">
      <h3 class="service__name"><svg viewBox="0 0 10 10"><circle cx="3.4" cy="3" r="1.7" fill="#fff"/><circle cx="7" cy="3" r="1.5" fill="#fff"/><path d="M0.5 9a3 3 0 0 1 6 0zM6.8 9a2.6 2.6 0 0 1 2.9-3.6V9z" fill="#fff"/></svg>Tenant Screening</h3>
      <p class="service__text">We don't just find someone to rent your home—we find the best renters. We screen all applications using fair housing guidelines to protect you.</p>
    </div>
    <div class="service">
      <h3 class="service__name"><svg viewBox="0 0 10 10"><text x="5" y="9" text-anchor="middle" font-size="10" font-weight="700" fill="#fff" font-family="Mulish,sans-serif">$</text></svg>Rent Collection</h3>
      <p class="service__text">Stop guessing when you'll receive your rental earnings every month and say hello to consistent payments. We keep your tenants current.</p>
    </div>
    <div class="service">
      <h3 class="service__name"><svg viewBox="0 0 10 10"><path d="M1.5 8.5 6 4" stroke="#fff" stroke-width="1.6" stroke-linecap="round"/><path d="M5.5 2.2a2 2 0 0 1 2.8-.6L7 3l.3 1 1 .3 1.4-1.3a2 2 0 0 1-2.9 2.4z" fill="#fff"/></svg>Maintenance</h3>
      <p class="service__text">Still scrambling to respond to repair requests every time you receive a tenant call? Let us coordinate repair work on your behalf!</p>
    </div>
    <div class="service">
      <h3 class="service__name"><svg viewBox="0 0 10 10"><circle cx="4" cy="4" r="2.7" fill="none" stroke="#fff" stroke-width="1.4"/><path d="M6 6l3 3" stroke="#fff" stroke-width="1.6" stroke-linecap="round"/></svg>Property Inspections</h3>
      <p class="service__text">Inspections form an important part of our proactive property management approach. We visit every home in our portfolio regularly.</p>
    </div>
    <div class="service">
      <h3 class="service__name"><svg viewBox="0 0 10 10"><path d="M1 1v8h8" stroke="#fff" stroke-width="1" fill="none"/><rect x="2.6" y="5" width="1.2" height="3" fill="#fff"/><rect x="4.6" y="3" width="1.2" height="5" fill="#fff"/><rect x="6.6" y="4" width="1.2" height="4" fill="#fff"/></svg>Financial Reporting</h3>
      <p class="service__text">Keep a handle on your real estate performance. We generate monthly statements so you can review income &amp; expenses at a moment's notice.</p>
    </div>
    <div class="service">
      <h3 class="service__name"><svg viewBox="0 0 10 10"><path d="M5 .8 1.5 2v3c0 2.2 1.6 3.5 3.5 4.2C6.9 8.5 8.5 7.2 8.5 5V2z" fill="#fff"/></svg>Evictions</h3>
      <p class="service__text">When things go wrong inside your rental home, rest easy with the experts on your side. We will handle evictions for you &amp; find new renters when its over.</p>
    </div>
    <div class="service">
      <h3 class="service__name"><svg viewBox="0 0 10 10"><path d="M5 1v8M2.5 9h5M1 2.5h8" stroke="#fff" stroke-width=".9"/><path d="M.6 6 2 2.8 3.4 6zM6.6 6 8 2.8 9.4 6z" fill="none" stroke="#fff" stroke-width=".8"/></svg>Legal Guidance</h3>
      <p class="service__text">Don't accidentally violate one of the many ordinances and housing laws governing your relationship with your tenants. Let us keep you compliant.</p>
    </div>
  </div>

  <div class="back-brand">
    <span class="brand__name">BRAMBLECREST</span>
    <span class="brand__tag">PROPERTY MANAGEMENT</span>
  </div>

  <div class="stamp-box"></div>

  <div class="address-block">
    <p class="address-block__to">TO</p>
    <div class="address-line"></div>
    <div class="address-line"></div>
    <div class="address-line"></div>
    <div class="address-line"></div>
  </div>

  <div class="back-contact">
    <p class="back-contact__phone">(806)555-0147</p>
    <p class="back-contact__web">www.bramblecrestpm.com</p>
    <p class="back-contact__address">2387 Hollow Pine Road, Lubbock, TX 79852</p>
  </div>
</section>

</body>
</html>
```